Business Card Design for Varomir Facility Services

We are looking for a Business Card Design for the Company "Varomir Facility Services."
Front side:
- Company Logo (small)
- Company Name, address, pohone, website and personal data.
- white background, for text e.g. company colors (blue or green like in the logo)
Please use following data:
Company data:
Varomir Facility Services Kostelac
Birkenhaldweg 14
6347 Rennbach
www.varomir-fs.ch
Person data:
Tarik Kostelac
Geschäftsführer
+41 76 519 47 83
info@varomir-fs.ch
Back side:
could be colored in blue or green
please use a big logo sing and some smaller icons to say what is all beeing offered in facility services, like cleaning, maintenance cleaning
industrial cleaning, caretaking, gardening, disposal. There is no need for everyone of the icons if there are similar or an icon is standing for more of them.
colors to use:
blue: HEX 246BB0
green: HEX 52B33E

```html
<!DOCTYPE html>
<html lang="de">
<head>
<meta charset="utf-8">
<title>Varomir Facility Services – Visitenkarte</title>
<link rel="stylesheet" href="https://fonts.googleapis.com/css2?family=Lato:ital,wght@0,400;0,700;0,900;1,400&display=swap">
<style>
  :root {
    --brand-green: #52B33E;
    --brand-blue: #246BB0;
    --icon-blue: #3a7cc4;
    --text-grey: #6b6b6b;
    --card-white: #ffffff;
    --backdrop: #2b2b2b;
  }
  * { box-sizing: border-box; margin: 0; padding: 0; }
  html, body {
    width: 1200px; height: 900px; overflow: hidden;
    background: var(--backdrop);
    font-family: "Lato", sans-serif;
  }
  .sheet {
    width: 1200px; height: 900px;
    display: flex; flex-direction: column; align-items: center; justify-content: center;
    gap: 30px;
  }
  .card {
    position: relative;
    width: 640px; height: 410px;
    border-radius: 26px;
    overflow: hidden;
    box-shadow: 0 12px 30px rgba(0,0,0,.45);
  }

  /* Back side */
  .card--back { background: var(--brand-green); color: var(--card-white); }
  .back-logo {
    position: absolute; left: 0; right: 0; top: 95px;
    display: flex; align-items: center; justify-content: center; gap: 18px;
  }
  .logo-dot {
    width: 58px; height: 58px; border-radius: 50%;
    background: var(--card-white);
  }
  .back-logo .logo-name {
    font-weight: 900; font-size: 44px; letter-spacing: 3px; line-height: 1;
    text-transform: uppercase;
  }
  .back-logo .logo-name small {
    display: block; font-size: 17px; letter-spacing: 6px; margin-top: 8px; font-weight: 900;
  }
  .service-list {
    position: absolute; left: 30px; right: 30px; bottom: 58px;
    display: flex; justify-content: space-between; list-style: none;
  }
  .service {
    display: flex; flex-direction: column; align-items: center; gap: 10px;
    font-size: 17px; white-space: nowrap;
  }
  .service-icon {
    width: 46px; height: 46px; border-radius: 50%;
    background: var(--icon-blue);
    box-shadow: 0 2px 4px rgba(0,0,0,.25);
  }

  /* Front side */
  .card--front { background: var(--card-white); }
  .front-logo {
    position: absolute; left: 44px; top: 40px;
    display: flex; align-items: center; gap: 12px;
    color: var(--brand-blue);
  }
  .front-logo .logo-dot { width: 40px; height: 40px; background: var(--brand-green); }
  .front-logo .logo-name {
    font-weight: 900; font-size: 30px; letter-spacing: 2px; line-height: 1; text-transform: uppercase;
  }
  .front-logo .logo-name small {
    display: block; font-size: 12px; letter-spacing: 4px; margin-top: 5px; font-weight: 900;
  }
  .rule { height: 1.5px; width: 210px; margin-bottom: 22px; }
  .rule--blue { background: var(--brand-blue); }
  .rule--green { background: var(--brand-green); }
  .person {
    position: absolute; left: 44px; top: 175px;
  }
  .person-name {
    color: var(--brand-green); font-weight: 900; font-size: 22px; text-transform: uppercase;
  }
  .person-role { color: var(--brand-blue); font-size: 22px; margin: 2px 0 12px; }
  .contact {
    display: flex; align-items: center; gap: 10px;
    color: var(--text-grey); font-size: 17px; line-height: 1.6; list-style: none;
  }
  .contact svg { width: 14px; height: 14px; fill: var(--brand-blue); flex: none; }
  .company {
    position: absolute; left: 330px; top: 205px;
  }
  .company-name { font-size: 23px; line-height: 1.15; color: var(--text-grey); }
  .company-name .accent { color: var(--brand-blue); }
  .company-address { font-size: 17px; color: var(--text-grey); margin-top: 6px; line-height: 1.35; font-style: normal; }
  .website { margin-top: 6px; }
  .website .domain { color: var(--brand-green); }
  .edge-band {
    position: absolute; left: 0; right: 0; bottom: 0; height: 16px;
    background: linear-gradient(90deg, var(--brand-green), var(--brand-blue));
  }
</style>
</head>
<body>
<main class="sheet">

  <section class="card card--back" aria-label="Rückseite">
    <div class="back-logo">
      <span class="logo-dot"></span>
      <div class="logo-name">Varomir<small>Facility Services</small></div>
    </div>
    <ul class="service-list">
      <li class="service"><span class="service-icon" role="img" aria-label="Icon: Unterhaltsreinigung"></span>Maintenance cleaning</li>
      <li class="service"><span class="service-icon" role="img" aria-label="Icon: Industriereinigung"></span>Industrial cleaning</li>
      <li class="service"><span class="service-icon" role="img" aria-label="Icon: Hauswartung"></span>Caretaking</li>
      <li class="service"><span class="service-icon" role="img" aria-label="Icon: Gartenpflege"></span>Gardening</li>
      <li class="service"><span class="service-icon" role="img" aria-label="Icon: Entsorgung"></span>Disposal</li>
    </ul>
  </section>

  <section class="card card--front" aria-label="Vorderseite">
    <div class="front-logo">
      <span class="logo-dot"></span>
      <div class="logo-name">Varomir<small>Facility Services</small></div>
    </div>

    <div class="person">
      <div class="rule rule--blue"></div>
      <p class="person-name">Tarik Kostelac</p>
      <p class="person-role">Geschäftsführer</p>
      <ul>
        <li class="contact">
          <svg viewBox="0 0 24 24" aria-hidden="true"><path d="M6.6 10.8a15.1 15.1 0 0 0 6.6 6.6l2.2-2.2a1 1 0 0 1 1-.25 11.4 11.4 0 0 0 3.6.57 1 1 0 0 1 1 1V20a1 1 0 0 1-1 1A17 17 0 0 1 3 4a1 1 0 0 1 1-1h3.5a1 1 0 0 1 1 1c0 1.25.2 2.45.57 3.57a1 1 0 0 1-.25 1z"/></svg>
          +41 76 519 47 83
        </li>
        <li class="contact">
          <svg viewBox="0 0 24 24" aria-hidden="true"><path d="M2 5h20v14H2zm2 2v.5l8 5 8-5V7l-8 5z"/></svg>
          info@varomir-fs.ch
        </li>
      </ul>
    </div>

    <div class="company">
      <div class="rule rule--green"></div>
      <p class="company-name"><span class="accent">Varomir Facility</span><br>Services Kostelac</p>
      <address class="company-address">Birkenhaldweg 14<br>6347 Rennbach</address>
      <p class="contact website">
        <svg viewBox="0 0 24 24" aria-hidden="true"><circle cx="12" cy="12" r="10"/><path d="M2 12h20M12 2c3 3 3 17 0 20M12 2c-3 3-3 17 0 20" stroke="#fff" stroke-width="1.5" fill="none"/></svg>
        <span>www.<span class="domain">varomir-fs</span>.ch</span>
      </p>
    </div>

    <div class="edge-band"></div>
  </section>

</main>
</body>
</html>
```